Harborline Renewal Business Card Design

Professional and clean design. The design colors should flow with the logo. Two-sided card with the website on the back which is:

www.HarborlineRenewal.example.

"Specializing in Water Damage Restoration"

On the front I need the name, email, phone, and logo.

Name: Darnell Quisby
Email: Darnell@HarborlineRenewal.example
Phone: 555-318-2046 for now

I only have the Preview and Thumbnail right now but should have the source files uploaded within a day or two.

Target Market(s)

Flood victims, home owners with water damage from busted pipes etc...

Industry/Entity Type

Business

Contact Information for Business Card

Name: Darnell Quisby

Font styles to use
Serif
Sans Serif

Requirements
Must have
• Business Card Details Info

```html
<!DOCTYPE html>
<html lang="en">
<head>
<meta charset="utf-8">
<title>Harborline Renewal Business Card</title>
<link href="https://fonts.googleapis.com/css2?family=Cinzel:wght@500;600&family=Open+Sans:wght@400&display=swap" rel="stylesheet">
<style>
  :root {
    --page: #eceef0;
    --card: #ffffff;
    --brand: #1f8fd0;
    --brand-pale: #a9dcf5;
    --band: #5cc1ef;
    --band-line: #4fb4e6;
    --ink: #1d3a4f;
    --grey: #555a5e;
    --rule: #c9cdd0;
  }
  * { margin: 0; padding: 0; box-sizing: border-box; }
  html, body { width: 1200px; height: 1120px; overflow: hidden; background: var(--page); }
  .canvas { position: relative; width: 1200px; height: 1120px; }
  .card {
    position: absolute; left: 160px; width: 880px; height: 503px;
    background: var(--card); box-shadow: 0 6px 18px rgba(0,0,0,.12);
    overflow: hidden;
  }
  .card--back { top: 40px; }
  .card--front { top: 577px; }

  /* back */
  .back-disc {
    position: absolute; left: 40px; top: 40px; width: 420px; height: 420px;
    border-radius: 50%; background: var(--brand-pale);
  }
  .back-name {
    position: absolute; left: 490px; top: 200px; width: 360px;
    font-family: "Cinzel", serif; font-weight: 600; color: var(--brand);
    font-size: 42px; line-height: 1.15; text-align: center; letter-spacing: 1px;
  }

  /* front */
  .front-disc {
    position: absolute; left: 400px; top: 30px; width: 80px; height: 80px;
    border-radius: 50%; background: var(--band);
  }
  .front-name {
    position: absolute; left: 0; right: 0; top: 125px; text-align: center;
    font-family: "Cinzel", serif; font-weight: 600; color: var(--brand);
    font-size: 42px; letter-spacing: 1px;
  }
  .tagline-band {
    position: absolute; left: 0; right: 0; top: 222px; height: 70px;
    border-top: 2px solid var(--band-line); border-bottom: 2px solid var(--band-line);
    padding: 5px 0;
  }
  .tagline-band__fill {
    height: 100%; background: var(--band);
    display: flex; align-items: center; justify-content: center;
    font-family: "Cinzel", serif; font-weight: 500; color: var(--ink);
    font-size: 24px; letter-spacing: 1px;
  }
  .holder {
    position: absolute; left: 40px; top: 345px; width: 420px; text-align: right;
    font-family: "Cinzel", serif;
  }
  .holder__name { color: var(--brand); font-size: 32px; font-weight: 600; }
  .holder__title { color: var(--grey); font-size: 26px; font-weight: 500; margin-top: 2px; }
  .divider {
    position: absolute; left: 482px; top: 330px; width: 2px; height: 110px; background: var(--rule);
  }
  .contacts {
    position: absolute; left: 502px; top: 330px; list-style: none;
    font-family: "Open Sans", sans-serif; font-size: 19px; color: #333;
  }
  .contacts li { display: flex; align-items: center; height: 36px; gap: 10px; }
  .contacts svg { width: 18px; height: 18px; flex: none; }
</style>
</head>
<body>
<div class="canvas">
  <section class="card card--back" aria-label="Card back">
    <div class="back-disc"></div>
    <div class="back-name">Harborline<br>Renewal</div>
  </section>

  <section class="card card--front" aria-label="Card front">
    <div class="front-disc"></div>
    <div class="front-name">Harborline Renewal</div>
    <div class="tagline-band">
      <div class="tagline-band__fill">Specializing in Water Damage Restoration</div>
    </div>
    <div class="holder">
      <div class="holder__name">Darnell Quisby</div>
      <div class="holder__title">Title</div>
    </div>
    <div class="divider"></div>
    <ul class="contacts">
      <li>
        <svg viewBox="0 0 20 20" aria-hidden="true"><circle cx="10" cy="10" r="9" fill="none" stroke="var(--brand)" stroke-width="1.6"/><path d="M7 5.5c-1 1 0 5 3.5 8 1.5 1 2.8 1 3.3.4l.6-.8-2-1.6-1 .8c-1-.5-2.5-2-3-3l.8-1L7.8 5z" fill="var(--brand)"/></svg>
        555-318-2046
      </li>
      <li>
        <svg viewBox="0 0 20 20" aria-hidden="true"><rect x="2" y="5" width="16" height="11" rx="1.5" fill="var(--brand)"/><path d="M2.5 6l7.5 5.5L17.5 6" fill="none" stroke="#fff" stroke-width="1.4"/></svg>
        Darnell@HarborlineRenewal.example
      </li>
      <li>
        <svg viewBox="0 0 20 20" aria-hidden="true"><circle cx="10" cy="10" r="8" fill="none" stroke="var(--brand)" stroke-width="1.6"/><ellipse cx="10" cy="10" rx="3.5" ry="8" fill="none" stroke="var(--brand)" stroke-width="1.3"/><path d="M2 10h16M3.5 6h13M3.5 14h13" stroke="var(--brand)" stroke-width="1.2"/></svg>
        www.HarborlineRenewal.example
      </li>
    </ul>
  </section>
</div>
</body>
</html>
```